Telecommunications/Power civil contractor needs business card design

Were a new telecommunications/power underground civil contractor that is looking for a new business card design. Our company colours are silver or grey and orange. Feel free to use the white background logo or the black background logo.

Target Market(s)

Local contractors, utility companies, private sector mining/energy companies, developers.

Industry/Entity Type

Telecommunications

Contact Information for Business Card

Each card will need the following info:
Persons name:
Title:
E-mail:
Phone number:
Shop Address:
Mailing Address:

Requirements
Must have
• Each card will need the following info:
• Persons name:
• Title:
• E-mail:
• Phone number:
• Shop Address:
• Mailing Address:

```html
<!DOCTYPE html>
<html lang="en">
<head>
<meta charset="utf-8">
<title>Volt Line Civil Works – Business Card</title>
<link rel="stylesheet" href="https://fonts.googleapis.com/css2?family=Open+Sans:wght@400;600;700&display=swap">
<style>
  :root {
    --stage: #2b2b2b;
    --card-white: #ffffff;
    --card-black: #0b0b0b;
    --orange: #f15a22;
    --grey: #8a8a8a;
    --grey-light: #bdbdbd;
    --ink: #4a4a4a;
  }
  html, body {
    margin: 0;
    width: 1200px;
    height: 716px;
    overflow: hidden;
    background: var(--stage);
    font-family: "Open Sans", Arial, sans-serif;
  }
  .canvas {
    position: relative;
    width: 1200px;
    height: 716px;
  }
  .card {
    position: absolute;
    top: 210px;
    width: 520px;
    height: 297px;
    overflow: hidden;
    box-shadow: 0 12px 30px rgba(0,0,0,.45);
  }
  .card--front { left: 50px; background: var(--card-white); }
  .card--back  { left: 630px; background: var(--card-black); }

  .card__waves { position: absolute; inset: 0; }

  .brand {
    position: absolute;
    display: flex;
    flex-direction: column;
    align-items: center;
    gap: 6px;
  }
  .brand__mark {
    width: 34px;
    height: 34px;
    border: 3px solid var(--grey);
    border-radius: 50%;
    box-sizing: border-box;
  }
  .brand__name {
    font-weight: 700;
    color: var(--orange);
    text-align: center;
    line-height: 1.05;
    letter-spacing: .5px;
    text-transform: uppercase;
  }
  .card--front .brand { left: 180px; top: 22px; width: 200px; }
  .card--front .brand__name { font-size: 17px; }
  .card--back .brand { left: 0; right: 0; top: 92px; }
  .card--back .brand__mark { width: 48px; height: 48px; }
  .card--back .brand__name { font-size: 24px; }

  .person {
    position: absolute;
    left: 34px;
    top: 112px;
  }
  .person__name {
    margin: 0;
    font-size: 17px;
    font-weight: 700;
    color: var(--orange);
    text-transform: uppercase;
  }
  .person__title {
    margin: 4px 0 0;
    font-size: 13px;
    color: var(--ink);
  }
  .contact {
    position: absolute;
    left: 214px;
    top: 112px;
    padding-left: 14px;
    border-left: 1px solid var(--grey);
    font-size: 12.5px;
    line-height: 1.5;
    color: var(--ink);
  }
  .contact p { margin: 0; display: flex; align-items: center; gap: 6px; }
  .contact svg { width: 12px; height: 12px; fill: var(--orange); flex: none; }
</style>
</head>
<body>
<main class="canvas">

  <section class="card card--front" aria-label="Business card front">
    <svg class="card__waves" viewBox="0 0 520 297" aria-hidden="true">
      <path d="M0 150 C150 158 250 250 520 268 L520 297 L0 297 Z" fill="var(--orange)"/>
      <path d="M0 232 C190 212 320 246 520 258 L520 272 C320 262 190 232 0 252 Z" fill="var(--card-white)"/>
      <path d="M150 297 C250 262 380 262 520 276 L520 284 C380 272 260 274 190 297 Z" fill="var(--grey)"/>
    </svg>

    <div class="brand">
      <span class="brand__mark"></span>
      <span class="brand__name">Volt Line<br>Civil Works Inc</span>
    </div>

    <div class="person">
      <p class="person__name">Morgan Hale</p>
      <p class="person__title">Managing Director</p>
    </div>

    <div class="contact">
      <p>N. 8 Sample Road,</p>
      <p>Suite 200, Lakeview, WA 00000</p>
      <p><svg viewBox="0 0 24 24"><path d="M6.6 10.8a15 15 0 0 0 6.6 6.6l2.2-2.2a1 1 0 0 1 1-.25 11.4 11.4 0 0 0 3.6.57 1 1 0 0 1 1 1V20a1 1 0 0 1-1 1A17 17 0 0 1 3 4a1 1 0 0 1 1-1h3.5a1 1 0 0 1 1 1c0 1.25.2 2.45.57 3.57a1 1 0 0 1-.25 1Z"/></svg>555.010.2040</p>
      <p><svg viewBox="0 0 24 24"><path d="M2 5h20v14H2Z M2 5l10 8 10-8" fill="var(--orange)"/><path d="M3 6l9 7 9-7" stroke="#fff" stroke-width="1.6" fill="none"/></svg>info@voltlinecivil.com</p>
    </div>
  </section>

  <section class="card card--back" aria-label="Business card back">
    <div class="brand">
      <span class="brand__mark"></span>
      <span class="brand__name">Volt Line<br>Civil Works Inc</span>
    </div>
  </section>

</main>
</body>
</html>
```